Private practice for psychiatry and psychotherapy needs a business card and logo

I need a logo and business card design for my private practice for psychiatry and psychotherapy. The optional names for my practice are: Vorsteling Praktijk voor Psychiatrie en Psychotherapie, or short: Praktijk Vorsteling.
I am a (child and adolescent) psychiatrist and psychotherapist. I diagnose and treat infants, children, adolescents and adults with psychiatric symptoms/disorders. I also give supervision to colleagues about their own treatments. My work is characterised by personal involvement, transparence, creativity and professionality.
I would like to have an appealing, light and bright, yet basic design that invites people (both children and adults) to contact me, gives trust and hope, without loosing professional appearance.
I uploaded my contact information which should not necessarily be all included (in this form) on the card as long as people know how to contact me. Please feel free to be creative!
Please note that my website is only temporarely and need a new design and update too!

Target Market(s)

Clients and patients (children, adolescents, adults) with psychiatric symptoms who need diagnosis and treatment. I work with private clients and patients through medical insurances.

Industry/Entity Type

Mental Health

Contact Information for Business Card

Dr. Ilse Vorsteling-ter Haaf
Psychiater/Kinder- en Jeugdpsychiater
Jorisvan Heultstraat 14
3071 PW Rotterdam
t: 06-58190274
e: info@praktijkvorsteling.nl
i: www.praktijkvorsteling.nl

Logo Text

Praktijk Vorsteling voor Psychiatrie en Psychotherapie; or short: Praktijk Vorsteling

Font styles to use
Sans Serif
Other font styles liked:
• up to designer

Requirements
Must have
• Appealing, light, bright, creative, trustful, professional and unique.

```html
<!DOCTYPE html>
<html lang="nl">
<head>
<meta charset="utf-8">
<title>Praktijk Vorsteling – visitekaartje</title>
<link rel="stylesheet" href="https://fonts.googleapis.com/css2?family=Open+Sans:wght@400;600&family=Roboto+Condensed:wght@700&family=Roboto:wght@400&display=swap">
<style>
  :root {
    --bg: #ececec;
    --teal: #62c6c6;
    --blue: #42a3dc;
    --accent: #3fa9df;
    --ink: #3a3a3a;
    --muted: #5f5f5f;
    --rule: #a9a9a9;
    --white: #ffffff;
  }
  * { box-sizing: border-box; margin: 0; padding: 0; }
  html, body { width: 1200px; height: 1000px; overflow: hidden; background: var(--bg); }
  body { position: relative; font-family: "Open Sans", sans-serif; }

  .card {
    position: absolute;
    left: 220px;
    width: 760px;
    height: 434px;
    border-radius: 22px;
    overflow: hidden;
    box-shadow: 0 6px 18px rgba(0,0,0,0.12);
  }

  /* Front */
  .card--front {
    top: 50px;
    background: linear-gradient(90deg, var(--teal) 0%, var(--blue) 100%);
    display: flex;
    flex-direction: column;
    align-items: center;
    justify-content: center;
    gap: 26px;
  }
  .brand-dot {
    width: 74px; height: 74px;
    border-radius: 50%;
    border: 2px solid var(--white);
  }
  .card--front .brand-name {
    font-family: "Open Sans", sans-serif;
    font-weight: 400;
    font-size: 27px;
    letter-spacing: 1px;
    color: var(--white);
  }

  /* Back */
  .card--back {
    top: 520px;
    background: var(--white);
  }
  .brand {
    position: absolute;
    top: 40px;
    right: 48px;
    display: flex;
    flex-direction: column;
    align-items: center;
    gap: 12px;
  }
  .brand .brand-dot {
    width: 52px; height: 52px;
    border-color: var(--accent);
  }
  .brand .brand-name {
    font-family: "Open Sans", sans-serif;
    font-weight: 400;
    font-size: 18px;
    letter-spacing: 0.5px;
    color: var(--ink);
  }
  .accent-bar {
    position: absolute;
    left: 0; top: 136px;
    width: 20px; height: 44px;
    background: var(--accent);
  }
  .person {
    position: absolute;
    left: 70px; top: 134px;
  }
  .person__name {
    font-family: "Roboto Condensed", sans-serif;
    font-weight: 700;
    font-size: 27px;
    color: var(--ink);
    letter-spacing: 0.3px;
  }
  .person__role {
    font-family: "Roboto", sans-serif;
    font-size: 18px;
    color: var(--accent);
    margin-top: 2px;
  }
  .rule {
    position: absolute;
    left: 70px; right: 60px; top: 218px;
    height: 2px;
    background: var(--rule);
  }
  .contact {
    position: absolute;
    left: 34px; top: 238px;
    list-style: none;
  }
  .contact li {
    display: flex;
    align-items: center;
    gap: 14px;
    font-size: 18px;
    color: var(--muted);
    height: 30px;
  }
  .contact svg { width: 16px; height: 16px; flex: none; }
  .contact .hl { color: var(--accent); }
  .rule--lower {
    top: 338px;
    left: 300px;
  }
  .address {
    position: absolute;
    right: 60px; top: 352px;
    text-align: right;
    font-size: 18px;
    line-height: 28px;
    color: var(--muted);
  }
  .address svg {
    position: absolute;
    right: -34px; top: 4px;
    width: 20px; height: 20px;
  }
</style>
</head>
<body>

<section class="card card--front" aria-label="Voorkant visitekaartje">
  <span class="brand-dot" aria-hidden="true"></span>
  <p class="brand-name">PRAKTIJK VORSTELING</p>
</section>

<section class="card card--back" aria-label="Achterkant visitekaartje">
  <div class="brand">
    <span class="brand-dot" aria-hidden="true"></span>
    <p class="brand-name">PRAKTIJK VORSTELING</p>
  </div>

  <span class="accent-bar" aria-hidden="true"></span>
  <div class="person">
    <h1 class="person__name">DR. ILSE VORSTELING-TER HAAF</h1>
    <p class="person__role">Psychiater/Kinder- en Jeugdpsychiater</p>
  </div>
  <span class="rule" aria-hidden="true"></span>

  <ul class="contact">
    <li>
      <svg viewBox="0 0 16 16" aria-hidden="true"><path fill="#3fa9df" d="M3.5 1.5l2.5 2.5-1.5 2a8 8 0 0 0 5.5 5.5l2-1.5 2.5 2.5-1.8 2C7 14 2 9 1.5 3.3z"/></svg>
      06-58190274
    </li>
    <li>
      <svg viewBox="0 0 16 16" aria-hidden="true"><rect x="1" y="3" width="14" height="10" rx="1" fill="#3fa9df"/><path d="M1.5 3.5L8 9l6.5-5.5" stroke="#fff" stroke-width="1.3" fill="none"/></svg>
      info@praktijkvorsteling.nl
    </li>
    <li>
      <svg viewBox="0 0 16 16" aria-hidden="true"><circle cx="9.5" cy="6.5" r="4.5" stroke="#3fa9df" stroke-width="2" fill="none"/><path d="M6 10l-4.5 4.5" stroke="#3fa9df" stroke-width="2.2"/></svg>
      <span>www.<span class="hl">praktijkvorsteling</span>.nl</span>
    </li>
  </ul>

  <span class="rule rule--lower" aria-hidden="true"></span>

  <address class="address" style="font-style:normal">
    <svg viewBox="0 0 20 20" aria-hidden="true"><path d="M2 17L18 3l-3 14-5-4z" fill="none" stroke="#3fa9df" stroke-width="1.5" stroke-linejoin="round"/></svg>
    Jorisvan Heultstraat 14<br>3071 PW Rotterdam
  </address>
</section>

</body>
</html>
```